website design for M&T Electric

A portfolio website for a high end commercial and residential electrical contracting company. The current site mandtelectric.example does not represent the current direction but the images in the gallery give you an idea of the work we do. Current logo will be uploaded shortly but is black text on white background.
Target Market(s)
General Contractors, Residential Home Owners, clients intersted in Velmora home automation.
Industry/Entity Type
Electrician
Coding
Coded - Design and coding required
Number of Pages Required
2 page
Font styles to use
Sans Serif
Colors
Designer to choose colors to be used in the design.
Requirements
Must have
- Portfolio section highlighting different service areas and products (Velmora Housepilot, etc)

```html
<!DOCTYPE html>
<html lang="en">
<head>
<meta charset="utf-8">
<title>M&amp;T Electric</title>
<link href="https://fonts.googleapis.com/css2?family=Roboto:ital,wght@0,300;0,400;0,500;0,700;0,900;1,400&display=swap" rel="stylesheet">
<style>
:root{
  --navy:#1b2d55;
  --navy-deep:#14213f;
  --footer:#1a2440;
  --footer-bar:#10182c;
  --ink:#1e1e1e;
  --muted:#8a8a8a;
  --line:#e2e2e2;
  --white:#ffffff;
  --footer-text:#c9cfdc;
}
*{margin:0;padding:0;box-sizing:border-box}
html,body{width:1200px;height:3237px;overflow:hidden}
body{font-family:"Roboto",Arial,sans-serif;color:var(--ink);background:var(--white);position:relative}
.abs{position:absolute}

/* header */
.site-header{left:0;top:0;width:1200px;height:123px;background:linear-gradient(#262626,#0b0b0b)}
.site-name{left:99px;top:42px;font-family:"Roboto",Arial,sans-serif;font-size:34px;font-weight:300;color:var(--white);letter-spacing:2px;text-transform:uppercase}
.nav{right:92px;top:58px;display:flex;gap:48px;font-size:14px;color:#cfcfcf;align-items:center}

/* hero */
.hero{left:0;top:123px;width:1200px;height:595px;background:linear-gradient(180deg,#8ab3d6 0%,#5d7fa7 40%,#2d3e5c 75%,#1c2233 100%)}
.hero-title{left:0;top:328px;width:1200px;text-align:center;font-size:37px;font-weight:300;color:var(--white);line-height:48px}
.hero-arrow{width:52px;height:52px;border:2px solid rgba(255,255,255,.8);border-radius:50%;top:346px}
.hero-curve{left:0;top:600px}

/* welcome */
.section-title{left:0;width:1200px;text-align:center;font-size:29px;font-weight:500;letter-spacing:.5px;text-transform:uppercase}
.intro{left:180px;width:840px;text-align:center;font-size:12px;line-height:25px;color:var(--muted)}
.service-card{top:917px;width:309px;height:248px;border:1px solid var(--line);text-align:center}
.service-icon{top:-62px;left:92px;width:124px;height:124px;border-radius:50%;background:var(--navy);border:5px solid #fff;box-shadow:0 0 0 1px var(--line)}
.service-icon svg{position:absolute;left:37px;top:34px}
.service-name{position:absolute;top:78px;width:100%;font-size:19px;font-weight:500;text-transform:uppercase}
.service-text{position:absolute;top:116px;left:20px;right:20px;font-size:12px;line-height:23px;color:var(--muted)}
.read-more{position:absolute;top:204px;width:100%;font-size:12px;font-weight:700;text-transform:uppercase}

/* about */
.about{left:0;top:1252px;width:1200px;height:373px;background:linear-gradient(180deg,#2a3c66,#1b2a4d 60%,#243556)}
.about-title{left:0;top:1300px;width:1200px;text-align:center;font-size:56px;font-weight:300;color:var(--white)}
.about-text{left:150px;top:1393px;width:900px;text-align:center;font-size:14.5px;line-height:23px;color:#e4e8f0}
.btn-outline{left:494px;top:1500px;width:212px;height:50px;border:2px solid #fff;color:#fff;font-size:17px;font-weight:500;text-align:center;line-height:46px;text-transform:uppercase}

/* gallery */
.gallery-tile{width:231px;height:192px;display:flex;align-items:center;justify-content:center;text-align:center;color:#fff;font-weight:900;font-size:27px;line-height:30px;letter-spacing:1.5px;text-transform:uppercase;text-shadow:0 2px 4px rgba(0,0,0,.6)}

/* testimonials */
.testimonials{left:0;top:2249px;width:1200px;height:326px;background:var(--navy)}
.quote-disc{left:99px;top:2363px;width:145px;height:117px;border-radius:60px;background:#e9e9e9}
.avatar{left:173px;top:2363px;width:115px;height:117px;border-radius:50%;background:linear-gradient(#d8d8d8,#8c8c8c);border:3px solid #fff}
.quote-text{left:309px;top:2376px;width:795px;font-size:13px;font-style:italic;line-height:21px;color:#e9edf5}
.person{left:309px;top:2452px;font-size:13px;font-weight:500;color:#fff;text-transform:uppercase;line-height:24px}
.person span{display:block;font-weight:400;color:#c9d0de}
.dots{left:566px;top:2515px;display:flex;gap:6px}
.dots i{width:9px;height:9px;border-radius:50%;border:1.5px solid #fff}
.dots i.on{background:#fff}

/* clients */
.client{top:2756px;width:154px;height:95px;border:1px solid var(--line);display:flex;align-items:center;justify-content:center;gap:7px;font-size:15px;font-weight:500;color:#444}
.client b{width:16px;height:16px;border-radius:50%;background:#444;display:block}
.slide-arrow{top:2785px}

/* footer */
.footer{left:0;top:2905px;width:1200px;height:272px;background:var(--footer)}
.footer-bar{left:0;top:3177px;width:1200px;height:60px;background:var(--footer-bar)}
.f-head{font-size:13px;font-weight:700;color:#fff;text-transform:uppercase;top:2948px}
.f-list{top:2980px;list-style:none;font-size:11px;color:var(--footer-text);line-height:27px}
.news-text{left:253px;top:2978px;width:260px;font-size:11px;line-height:20px;color:var(--footer-text)}
.news-input{left:253px;top:3030px;width:242px;height:42px;background:#fff;font-size:11px;color:#888;padding:14px 12px}
.news-btn{left:253px;top:3088px;width:92px;height:40px;background:#000;color:#fff;font-size:12px;text-align:center;line-height:40px;text-transform:uppercase}
.contact{left:939px;top:2980px;font-size:11px;color:var(--footer-text);line-height:27px}
.contact .row{display:flex;align-items:center;gap:8px}
.copy{left:99px;top:3199px;font-size:11px;color:var(--footer-text)}
.social{left:776px;top:3196px;display:flex;gap:16px;align-items:center;font-size:11px;color:var(--footer-text)}
.social i{width:12px;height:12px;border-radius:50%;background:var(--footer-text);display:block}
</style>
</head>
<body>

<header class="abs site-header">
  <div class="abs site-name">M&amp;T Electric</div>
  <nav class="abs nav">
    <span>Home</span><span>Gallery</span><span>Specialty Services</span><span>About</span><span>Contact</span>
    <svg width="14" height="14" viewBox="0 0 14 14"><circle cx="6" cy="6" r="4.5" fill="none" stroke="#cfcfcf" stroke-width="2"/><line x1="9.5" y1="9.5" x2="13" y2="13" stroke="#cfcfcf" stroke-width="2"/></svg>
  </nav>
</header>

<section class="abs hero" role="img" aria-label="Modern apartment buildings lit at dusk"></section>
<h1 class="abs hero-title">We are a high end commercial and residential electrical<br>contracting company</h1>
<div class="abs hero-arrow" style="left:22px"><svg width="48" height="48"><polyline points="28,16 20,24 28,32" fill="none" stroke="#fff" stroke-width="2.5"/></svg></div>
<div class="abs hero-arrow" style="left:1130px"><svg width="48" height="48"><polyline points="20,16 28,24 20,32" fill="none" stroke="#fff" stroke-width="2.5"/></svg></div>
<svg class="abs hero-curve" width="1200" height="120" viewBox="0 0 1200 120"><path d="M0 118 Q560 20 1200 60 L1200 120 L0 120 Z" fill="#fff"/></svg>

<h2 class="abs section-title" style="top:722px">Welcome to M&amp;T Electric</h2>
<p class="abs intro" style="top:772px">Sed ut perspiciatis unde omnis iste natus error sit voluptatem accusantium doloremque laudantium, totam rem aperiam, eaque ipsa quae ab illo inventore veritatis et quasi architecto beatae vitae dicta sunt explicabo.</p>

<article class="abs service-card" style="left:99px">
  <div class="abs service-icon"><svg width="40" height="46" viewBox="0 0 40 46"><rect x="8" y="6" width="24" height="40" fill="#fff"/><rect x="15" y="0" width="10" height="8" fill="#fff"/><g fill="#1b2d55"><rect x="12" y="12" width="4" height="4"/><rect x="18" y="12" width="4" height="4"/><rect x="24" y="12" width="4" height="4"/><rect x="12" y="20" width="4" height="4"/><rect x="18" y="20" width="4" height="4"/><rect x="24" y="20" width="4" height="4"/><rect x="12" y="28" width="4" height="4"/><rect x="24" y="28" width="4" height="4"/><rect x="17" y="36" width="6" height="10"/></g></svg></div>
  <h3 class="service-name">Commercial</h3>
  <p class="service-text">Sed ut perspiciatis unde omnis iste natus error sit voluptatem accusantium doloremque laudantium, totam rem aperiam, eaque ipsa quae.</p>
  <div class="read-more">Read more &#10140;</div>
</article>
<article class="abs service-card" style="left:445px">
  <div class="abs service-icon"><svg width="46" height="44" viewBox="0 0 46 44"><polygon points="23,0 46,20 40,20 40,44 6,44 6,20 0,20" fill="#fff"/><rect x="13" y="24" width="8" height="8" fill="#1b2d55"/><rect x="26" y="28" width="8" height="16" fill="#1b2d55"/></svg></div>
  <h3 class="service-name">Residential</h3>
  <p class="service-text">Sed ut perspiciatis unde omnis iste natus error sit voluptatem accusantium doloremque laudantium, totam rem aperiam, eaque ipsa quae.</p>
  <div class="read-more">Read more &#10140;</div>
</article>
<article class="abs service-card" style="left:792px">
  <div class="abs service-icon"><svg width="50" height="40" viewBox="0 0 50 40"><g fill="#fff"><rect x="0" y="14" width="10" height="26"/><rect x="12" y="4" width="11" height="36"/><rect x="25" y="10" width="10" height="30"/><rect x="37" y="18" width="13" height="22"/></g><g fill="#1b2d55"><rect x="15" y="10" width="2" height="26"/><rect x="19" y="10" width="2" height="26"/><rect x="28" y="15" width="2" height="22"/><rect x="3" y="19" width="2" height="18"/><rect x="41" y="22" width="2" height="14"/><rect x="45" y="22" width="2" height="14"/></g></svg></div>
  <h3 class="service-name">Landscape</h3>
  <p class="service-text">Sed ut perspiciatis unde omnis iste natus error sit voluptatem accusantium doloremque laudantium, totam rem aperiam, eaque ipsa quae.</p>
  <div class="read-more">Read more &#10140;</div>
</article>

<section class="abs about" role="img" aria-label="High-rise buildings under construction with cranes, tinted navy"></section>
<h2 class="abs about-title">About Us</h2>
<p class="abs about-text">M&amp;T Electric is a full service electrical contracting shop. We offer commercial, residential, light industrial, and agricultural services. We're Velmora Housepilot and Velmora Motorized Shades certified, as well as an authorized Stalwart Power generator dealer. We've served the Cedar Valley and South Central Montara area for over 18 years.</p>
<div class="abs btn-outline">More Information</div>

<h2 class="abs section-title" style="top:1674px">Our Gallery</h2>
<div class="abs gallery-tile" style="left:99px;top:1759px;background:linear-gradient(#5d7896,#6d5a48)" role="img" aria-label="Commercial building with stone facade">Commercial</div>
<div class="abs gallery-tile" style="left:356px;top:1759px;background:linear-gradient(#5a4a4e,#7a5a5a)" role="img" aria-label="Residential home roof framing">Residential</div>
<div class="abs gallery-tile" style="left:613px;top:1759px;background:linear-gradient(#8a8aa6,#4a4450)" role="img" aria-label="Landscape lighting at dusk">Landscape</div>
<div class="abs gallery-tile" style="left:870px;top:1759px;background:linear-gradient(#7d8276,#b9bcb3)" role="img" aria-label="Standby generator unit">Generators</div>
<div class="abs gallery-tile" style="left:99px;top:1972px;background:linear-gradient(#8ea9c9,#5b5a55)" role="img" aria-label="Office building with motorized shades">Velmora<br>Shades</div>
<div class="abs gallery-tile" style="left:356px;top:1972px;background:linear-gradient(#a6b0bb,#5a4a40)" role="img" aria-label="Building exterior with dimming system">Velmora<br>Dimming</div>
<div class="abs gallery-tile" style="left:613px;top:1972px;background:linear-gradient(#2c2c2c,#3f3f3f)" role="img" aria-label="LED light fixtures">LED<br>Lighting</div>
<div class="abs gallery-tile" style="left:870px;top:1972px;background:linear-gradient(#4d4a44,#7a6a58)" role="img" aria-label="Electrician working on a panel">Service<br>Calls</div>

<section class="abs testimonials"></section>
<h2 class="abs section-title" style="top:2310px;color:#fff">Client Testimonials</h2>
<div class="abs quote-disc"><svg width="70" height="60" style="margin:30px 0 0 12px"><text x="0" y="70" font-family="Georgia,serif" font-size="110" fill="#cfcfcf">&#8220;</text></svg></div>
<div class="abs avatar" role="img" aria-label="Client portrait"></div>
<p class="abs quote-text">Sed ut perspiciatis unde omnis iste natus error sit voluptatem accusantium doloremque laudantium, totam rem aperiam, eaque ipsa quae ab illo inventore veritatis et quasi architecto beatae vitae dicta sunt explicabo. Nemo enim ipsam voluptatem quia voluptas sit aspernatur aut odit aut fugit, sed quia consequuntur magni dolores eos qui ratione voluptatem sequi nesciunt.</p>
<div class="abs person">Daniel Reyes<span>City Name</span></div>
<div class="abs dots"><i></i><i class="on"></i><i></i><i></i></div>

<h2 class="abs section-title" style="top:2617px">Our Clients</h2>
<p class="abs intro" style="top:2671px">Neque porro quisquam est, qui dolorem ipsum quia dolor sit amet, consectetur, adipisci velit, sed quia non numquam eius modi tempora incidunt ut labore et dolore magnam aliquam quaerat voluptatem.</p>
<svg class="abs slide-arrow" style="left:52px" width="24" height="36"><polyline points="18,4 6,18 18,32" fill="none" stroke="#aaa" stroke-width="3"/></svg>
<div class="abs client" style="left:99px"><b></b>Tessaline</div>
<div class="abs client" style="left:268px"><b></b>Ledgerleaf Trade</div>
<div class="abs client" style="left:438px">Kindhaven</div>
<div class="abs client" style="left:607px"><b></b>Oldstone Trust</div>
<div class="abs client" style="left:776px"><b></b>Corvanta</div>
<div class="abs client" style="left:946px;font-size:13px"><b></b>Brightpath Training</div>
<svg class="abs slide-arrow" style="left:1126px" width="24" height="36"><polyline points="6,4 18,18 6,32" fill="none" stroke="#aaa" stroke-width="3"/></svg>

<footer class="abs footer"></footer>
<div class="abs f-head" style="left:99px">Links</div>
<ul class="abs f-list" style="left:99px"><li>Home</li><li>About Us</li><li>Services</li><li>Our Team</li><li>Clients</li><li>Blog</li></ul>
<div class="abs f-head" style="left:253px">Join Our Newsletter</div>
<p class="abs news-text">Excepteur sint occaecat cupidatat non proident, sunt in culpa qui</p>
<div class="abs news-input">Enter Your Email</div>
<div class="abs news-btn">Subscribe</div>
<div class="abs f-head" style="left:589px">Information</div>
<ul class="abs f-list" style="left:589px"><li>Terms &amp; Conditions</li><li>Privacy policy</li><li>Disclaimer</li><li>Contact us</li><li>Sitemap</li></ul>
<div class="abs f-head" style="left:786px">Why Us</div>
<ul class="abs f-list" style="left:786px"><li>Customers</li><li>Team</li><li>FAQ</li><li>News</li><li>Others</li></ul>
<div class="abs f-head" style="left:939px">Contact Info</div>
<div class="abs contact">
  <div>215 Hangar Lane</div><div>PO Box 1180</div><div>Ridgeford, MT 59001</div>
  <div class="row"><svg width="11" height="11" viewBox="0 0 12 12"><path d="M2 1 L4.5 1 L5.5 4 L4 5 Q5 7.5 7 8 L8 6.5 L11 7.5 L11 10 Q6 12 2 6 Q0.5 3 2 1Z" fill="#fff"/></svg>(555) 014-2234</div>
  <div class="row"><svg width="12" height="9" viewBox="0 0 12 9"><rect width="12" height="9" fill="#fff"/><polyline points="0,0 6,5 12,0" fill="none" stroke="#1a2440" stroke-width="1.2"/></svg>dwalker@mandtelectric.example</div>
</div>

<div class="abs footer-bar"></div>
<div class="abs copy">&copy; 2017. M&amp;T Electric. All rights reserved</div>
<div class="abs social">Connect with our social network :<i></i><i></i><i></i><i></i><i></i></div>

</body>
</html>
```